Business Card Design for company

We want new business cards. We'd like something different-- yet still highly professional. Our tagline is Providing leadership, delivering success. Stock photos are ok, as long as they are relevant and look upscale.

Target Market(s)

Architecture/Business Management Consulting/Engineering Consulting

Contact Information for Business Card

dark gray background with pops of blue might be good, but you tell me. You're the designers. Rounded corners might be nice, but again, you tell me.

Font styles to use
Serif
Sans Serif

Colors
3276b5
5c5c5c
9d9d9d
fbfbfb

Requirements
Nice to have
• Something different, but still very professional.

```html
<!DOCTYPE html>
<html lang="en">
<head>
<meta charset="utf-8">
<title>Orvenra Partners – Business Card</title>
<link rel="stylesheet" href="https://fonts.googleapis.com/css2?family=Lato:wght@400;700&family=Raleway:wght@500;600;700&display=swap">
<style>
  :root {
    --brand-blue: #3276b5;
    --mid-gray: #5c5c5c;
    --light-gray: #9d9d9d;
    --paper-white: #fbfbfb;
    --card-dark: #1b1c1e;
    --card-darker: #151617;
    --backdrop: #2a2a2b;
  }
  * { margin: 0; padding: 0; box-sizing: border-box; }
  html, body { width: 1200px; height: 1108px; overflow: hidden; }
  body {
    background: var(--backdrop);
    font-family: "Lato", sans-serif;
    position: relative;
  }
  .card {
    position: absolute;
    top: 194px;
    width: 400px;
    height: 720px;
    border-radius: 26px;
    background: var(--card-dark);
    overflow: hidden;
  }
  .card--front { left: 170px; }
  .card--back { left: 630px; background: var(--card-darker); }

  .wordmark {
    font-family: "Raleway", sans-serif;
    font-weight: 700;
    color: var(--brand-blue);
    text-align: center;
    letter-spacing: 1px;
  }
  .card--front .wordmark {
    margin-top: 150px;
    font-size: 52px;
    line-height: 1.05;
  }
  .wordmark__sub { display: block; font-size: 24px; letter-spacing: 4px; }

  .identity { margin-top: 90px; text-align: center; }
  .identity__name {
    color: var(--brand-blue);
    font-size: 26px;
    letter-spacing: 0.5px;
    text-transform: uppercase;
  }
  .identity__role { color: var(--light-gray); font-size: 20px; margin-top: 2px; }

  .icon-rule {
    display: flex; align-items: center; gap: 8px;
    margin: 20px 60px 14px;
  }
  .icon-rule__line { flex: 1; height: 1px; background: var(--mid-gray); }
  .icon-rule svg { display: block; }

  .contact { text-align: center; color: var(--paper-white); font-size: 20px; line-height: 1.35; }
  .contact--address { color: var(--light-gray); }
  .plain-rule { height: 1px; background: var(--mid-gray); margin: 14px 60px; }

  .card__backdrop {
    position: absolute; inset: 0;
    background: linear-gradient(160deg, #2a2b2d 0%, #1f2022 45%, var(--card-darker) 100%);
  }
  .back-lockup {
    position: absolute; left: 0; right: 0; bottom: 120px;
    text-align: center;
  }
  .card--back .wordmark { font-size: 60px; line-height: 1.05; }
  .card--back .wordmark__sub { font-size: 28px; }
  .tagline {
    margin-top: 24px;
    font-family: "Raleway", sans-serif;
    font-weight: 600;
    font-size: 22px;
    line-height: 1.25;
    color: var(--paper-white);
    text-transform: uppercase;
    letter-spacing: 0.5px;
  }
</style>
</head>
<body>
  <section class="card card--front" aria-label="Card front">
    <div class="wordmark">ORVENRA<span class="wordmark__sub">PARTNERS</span></div>

    <div class="identity">
      <p class="identity__name">Daniel Reyes</p>
      <p class="identity__role">Managing Director</p>
    </div>

    <div class="icon-rule">
      <span class="icon-rule__line"></span>
      <svg width="82" height="24" viewBox="0 0 82 24" aria-hidden="true">
        <circle cx="12" cy="12" r="11" fill="var(--brand-blue)"/>
        <path d="M8 7c1-1 2 0 2.5 1.2l.5 1.5-1 1c.6 1.3 1.5 2.2 2.8 2.8l1-1 1.5.5c1.2.5 2.2 1.5 1.2 2.5-1.5 1.5-4 .5-6-1.5S6.5 8.5 8 7z" fill="var(--card-dark)"/>
        <circle cx="41" cy="12" r="11" fill="var(--brand-blue)"/>
        <rect x="35" y="8" width="12" height="8" rx="1" fill="var(--card-dark)"/>
        <path d="M35.5 8.5l5.5 4 5.5-4" stroke="var(--brand-blue)" stroke-width="1.2" fill="none"/>
        <circle cx="70" cy="12" r="11" fill="var(--brand-blue)"/>
        <path d="M70 18s-4.5-4.6-4.5-7.5a4.5 4.5 0 0 1 9 0C74.5 13.4 70 18 70 18z" fill="var(--card-dark)"/>
        <circle cx="70" cy="10.5" r="1.6" fill="var(--brand-blue)"/>
      </svg>
      <span class="icon-rule__line"></span>
    </div>

    <div class="contact">
      <p>444 555 2190</p>
      <p>hello@orvenra.com</p>
      <p>www.orvenra.com</p>
    </div>
    <div class="plain-rule"></div>
    <div class="contact contact--address">
      <p>88 Harbor Lane,</p>
      <p>Westbrook, 40217</p>
    </div>
  </section>

  <section class="card card--back" aria-label="Card back">
    <div class="card__backdrop" role="img" aria-label="Faint repeating company name pattern across the card in dark gray tones"></div>
    <div class="back-lockup">
      <div class="wordmark">ORVENRA<span class="wordmark__sub">PARTNERS</span></div>
      <p class="tagline">Providing leadership<br>delivering success</p>
    </div>
  </section>
</body>
</html>
```